Ledger Lanternfox Powerpoint with Marshal Valorline Type Theme

Need powerpoint template with matching colors and different slide options. Logo and colors to be used can be found at ledgerlanternfox.example. Want brightly colored slide deck that is readable form the back of a room, but highlights colors. I will be incorporating Quizzap into the slides to gamify my presentations.

Target Market(s)

Tech

Industry/Entity Type

IT, specifically database, but crossing over to mental health in IT, important note this is not for a company, this is just for a professional building a brand

Font styles to use
Sans Serif

Colors
0054AA
0677BA
7BADD7
CADEEF
E8F1F8
EB3D1F
EC4F4E
F09395
F8D3D4
FCEDEE

Requirements
Must have
• My Logo in the bottom corner, front page, a thank your page, question page, content page, content page with two columns, content page with graphs, and icons to be used in the primary colors of the logos, About Me Page, Break Slides, Demo break slide
Should not have
• Lighter shades of colors, I want to pop out where colors are used, I want spacing and font size to be readable from the back of a room, most likely black text and white background

```html
<!DOCTYPE html>
<html lang="en">
<head>
<meta charset="utf-8">
<title>Ledger Lanternfox – Marshal Valorline Slide Theme</title>
<link rel="stylesheet" href="https://fonts.googleapis.com/css2?family=Poppins:wght@300;400;500;600;700&display=swap">
<style>
:root{
  --navy:#1b4585;
  --navy-deep:#133466;
  --ink:#0f2447;
  --red:#e8282b;
  --red-soft:#f5c9ca;
  --charcoal:#3d3d3d;
  --gray:#7d7d7d;
  --line:#e4e6ea;
  --canvas:#dcdcdc;
  --white:#ffffff;
  --text:#2a2a2a;
}
*{box-sizing:border-box;margin:0;padding:0}
html,body{width:1200px;height:3398px;overflow:hidden;background:var(--canvas)}
body{font-family:"Poppins",Arial,sans-serif;color:var(--text)}
.deck{position:absolute;left:10px;top:10px;display:grid;grid-template-columns:repeat(3,388px);grid-auto-rows:218px;gap:8px}
.slide{position:relative;overflow:hidden;background:var(--white)}
.bg-navy{background:var(--navy)}
.bg-charcoal{background:var(--charcoal)}
.bg-red{background:var(--red)}
.photo{position:absolute;inset:0;background:linear-gradient(135deg,#2a5597 0%,#1b4585 45%,#13336a 100%)}
.photo.light{background:linear-gradient(120deg,#c9d3df 0%,#8ea1b9 50%,#5c6f8a 100%)}
.abs{position:absolute}
.logo{position:absolute;display:flex;align-items:center;gap:4px;font-weight:700;font-size:9px;color:var(--white);white-space:nowrap}
.logo::before{content:"";width:12px;height:12px;border-radius:50%;background:var(--red)}
.logo.dark{color:var(--navy)}
.logo.big{font-size:22px;gap:10px}
.logo.big::before{width:34px;height:34px}
.url{font-size:6px;letter-spacing:1px;color:#dfe7f3}
.pill{position:absolute;background:var(--red);color:var(--white);border-radius:8px;font-size:5.5px;font-weight:600;text-align:center;line-height:12px;height:12px}
.hero{font-weight:600;color:var(--white);line-height:1.05}
.tiny{font-size:5px;line-height:1.45;color:#e9eef6}
.body{font-size:5px;line-height:1.5;color:#555}
.title{position:absolute;font-weight:600;font-size:15px;color:var(--navy)}
.title.center{left:0;right:0;text-align:center}
.title.white{color:var(--white)}
.dash{position:absolute;width:14px;height:3px;background:var(--red)}
.rail{position:absolute;top:0;bottom:0;right:0;width:22px;border-left:1px solid var(--line);background:var(--white)}
.rail.left{right:auto;left:0;border-left:0;border-right:1px solid var(--line)}
.rail::before{content:"";position:absolute;top:3px;left:5px;width:11px;height:11px;border-radius:50%;background:var(--navy)}
.rail span{position:absolute;top:50%;left:50%;transform:translate(-50%,-50%) rotate(90deg);font-size:6px;font-weight:700;color:var(--red);white-space:nowrap}
.rail.dark{background:var(--navy);border-color:#2f5a98}
.rail.dark::before{background:var(--white)}
.page-no{position:absolute;bottom:5px;right:28px;font-size:5px;color:#555}
.page-no.left{right:auto;left:28px}
.page-no.l{right:auto;left:6px}
.watermark{position:absolute;left:50%;top:58%;transform:translate(-50%,-50%);width:150px;height:110px;border-radius:50%;background:#eaf0f8;display:flex;align-items:center;justify-content:center;font-weight:700;font-size:13px;color:#f6d5d6}
.card{position:absolute;border-radius:3px;color:var(--white);text-align:center;padding:16px 6px 4px}
.card h4{font-size:5.5px;font-weight:600;margin-bottom:3px}
.card p{font-size:4.2px;line-height:1.45;opacity:.9}
.card .ic{position:absolute;top:-9px;left:50%;transform:translateX(-50%);width:18px;height:18px;border-radius:50%;background:var(--white);border:1.5px solid currentColor}
.c-red{background:var(--red)} .c-navy{background:var(--navy)} .c-deep{background:var(--ink)} .c-gray{background:var(--gray)}
.tbl{position:absolute;border-collapse:collapse;font-size:4.5px;color:#777;text-align:center}
.tbl th{background:var(--navy);color:var(--white);font-weight:500;height:11px}
.tbl td{height:10.5px;border-bottom:1px solid var(--line)}
.tbl .row-h{background:var(--navy);color:var(--white);text-align:left;padding-left:10px;border-bottom:1px solid #fff}
.tbl.redhead th{background:var(--red)}
.demo-ring{position:absolute;border-radius:50%;display:flex;flex-direction:column;align-items:center;justify-content:center;text-align:center;padding:0 24px}
.demo-ring h3{font-size:14px;font-weight:600;letter-spacing:1px;display:flex;align-items:center;gap:6px;margin-bottom:8px}
.demo-ring h3::before,.demo-ring h3::after{content:"";width:24px;height:1px;background:currentColor}
.qa-row{position:absolute;display:flex;gap:6px;align-items:flex-start}
.qa-row b{width:13px;height:13px;border-radius:2px;color:#fff;font-size:7px;text-align:center;line-height:13px;flex:none}
.qa-row p{font-size:4.5px;line-height:1.45;color:#555;width:112px}
.chev{position:absolute;top:92px;height:20px;width:58px;clip-path:polygon(0 0,85% 0,100% 50%,85% 100%,0 100%,12% 50%);color:#fff;font-size:5.5px;font-weight:600;display:flex;align-items:center;justify-content:center}
.step-text{position:absolute;top:128px;width:60px;text-align:center}
.step-text h5{font-size:5px;font-weight:600;color:var(--text);margin-bottom:2px}
.step-text p{font-size:3.8px;line-height:1.45;color:#777}
</style>
</head>
<body>
<main class="deck">

<!-- 1 cover -->
<section class="slide">
  <div class="photo" role="img" aria-label="Blue-tinted photo of a person at a laptop"></div>
  <div class="logo" style="left:150px;top:28px">Ledger Lanternfox</div>
  <div class="abs url" style="left:0;right:0;top:52px;text-align:center">www.ledgerlanternfox.example</div>
  <div class="abs hero" style="left:0;right:0;top:68px;text-align:center;font-size:24px">Presentation<br>Title Goes Here</div>
  <div class="abs" style="left:0;right:0;top:124px;text-align:center;font-size:8px;color:#fff">Sub Title Goes Here</div>
  <div class="pill" style="left:146px;top:182px;width:50px">Oct 2021</div>
</section>

<!-- 2 -->
<section class="slide">
  <div class="abs bg-navy" style="left:0;right:0;top:0;height:178px"></div>
  <div class="abs hero" style="left:20px;top:72px;font-size:20px;font-weight:500">TITLE OF<br>PRESENTATION</div>
  <div class="abs tiny" style="left:22px;top:138px">Here is A place for Credentials<br>Date: 2021 March</div>
  <div class="logo dark" style="left:8px;top:192px">Ledger Lanternfox</div>
  <div class="abs" style="right:38px;top:197px;font-size:6px;font-weight:600;color:var(--red)">Presenter Name</div>
</section>

<!-- 3 -->
<section class="slide">
  <div class="photo" role="img" aria-label="Blue-tinted photo of server racks"></div>
  <div class="logo" style="left:24px;top:60px">Ledger Lanternfox</div>
  <div class="abs hero" style="left:24px;top:86px;font-size:20px;font-weight:500">TITLE OF<br>PRESENTATION</div>
  <div class="abs tiny" style="left:25px;top:152px">Here is A place for Credentials<br>Date: 2021 March</div>
</section>

<!-- 4 -->
<section class="slide">
  <div class="photo light" role="img" aria-label="Photo of hands using a laptop on a desk"></div>
  <div class="abs" style="left:0;top:0;width:150px;height:218px;background:linear-gradient(90deg,#1b4585 0%,rgba(27,69,133,.6) 100%)"></div>
  <div class="logo" style="left:40px;top:48px;font-size:12px">Ledger Lanternfox</div>
  <div class="abs bg-red" style="left:100px;top:112px;width:300px;height:60px;clip-path:polygon(14% 0,100% 0,100% 100%,0 100%)"></div>
  <div class="abs hero" style="left:150px;right:20px;top:118px;text-align:center;font-size:18px">Presentation<br>Title Goes Here</div>
</section>

<!-- 5 -->
<section class="slide">
  <div class="abs" style="left:190px;top:40px;width:150px;height:110px;border-radius:50%;background:#eaf0f8;display:flex;align-items:center;justify-content:center;font-weight:700;font-size:13px;color:#f6d5d6">Ledger Lanternfox</div>
  <div class="logo dark" style="left:24px;top:48px">Ledger Lanternfox</div>
  <div class="abs" style="left:24px;top:80px;font-weight:600;font-size:22px;line-height:1.05;color:var(--navy)">Presentation<br>Title Goes Here</div>
  <div class="abs" style="left:25px;top:130px;font-size:8px;color:var(--red)">Sub Title Goes Here</div>
  <div class="pill" style="left:22px;top:172px;width:116px;letter-spacing:1px">www.ledgerlanternfox.example</div>
</section>

<!-- 6 -->
<section class="slide"><div class="logo dark" style="left:140px;top:24px">Ledger Lanternfox</div></section>
<!-- 7 -->
<section class="slide bg-navy"><div class="logo" style="left:140px;top:24px">Ledger Lanternfox</div></section>
<!-- 8 -->
<section class="slide bg-charcoal"><div class="logo" style="left:140px;top:24px">Ledger Lanternfox</div></section>
<!-- 9 -->
<section class="slide bg-red"><div class="logo" style="left:140px;top:24px;--x:0"><span style="display:none"></span>Ledger Lanternfox</div></section>

<!-- 10 quote -->
<section class="slide">
  <div class="abs" style="left:170px;top:40px;font-size:60px;font-weight:600;color:#c8c8c8;line-height:1">&ldquo;</div>
  <div class="pill" style="left:58px;top:142px;width:80px;height:14px;line-height:14px;font-size:6.5px">Your Name</div>
  <div class="page-no">10</div><div class="rail"><span>Ledger Lanternfox</span></div>
</section>

<!-- 11 about me -->
<section class="slide">
  <div class="abs" role="img" aria-label="Portrait placeholder with diagonal stripes" style="left:18px;top:40px;width:86px;height:86px;border-radius:50%;background:var(--navy)"></div>
  <svg class="abs" style="left:40px;top:148px" width="80" height="40" viewBox="0 0 80 40">
    <circle cx="4" cy="4" r="3" fill="var(--navy)"/><text x="12" y="6" font-size="4" fill="#e8282b">Here is a place for text</text>
    <circle cx="4" cy="18" r="3" fill="var(--navy)"/><text x="12" y="20" font-size="4" fill="#e8282b">Here is a place for text</text>
    <rect x="1" y="29" width="6" height="5" fill="var(--navy)"/><text x="12" y="34" font-size="4" fill="#e8282b">Here is a place for text</text>
  </svg>
  <div class="abs" style="left:152px;top:28px;font-size:7px;color:var(--red)">Manager</div>
  <div class="abs" style="left:152px;top:38px;font-size:13px;font-weight:600;color:var(--navy)">Name, Last Name</div>
  <div class="dash" style="left:152px;top:58px"></div>
  <p class="abs body" style="left:152px;top:70px;width:185px">Lorem ipsum dolor sit amet, consectetur adipiscing elit, sed do eiusmod tempor incididunt ut labore et dolore magna aliqua.</p>
  <p class="abs body" style="left:152px;top:110px;width:185px">Lorem ipsum dolor sit amet, consectetur adipiscing elit, sed do eiusmod tempor incididunt ut labore et dolore magna aliqua.</p>
  <div class="page-no">11</div><div class="rail"><span>Ledger Lanternfox</span></div>
</section>

<!-- 12 agenda -->
<section class="slide">
  <div class="abs bg-navy" style="left:0;top:0;width:152px;height:135px"></div>
  <ol class="abs" style="left:34px;top:28px;width:172px;height:170px;background:#fff;box-shadow:0 2px 8px rgba(0,0,0,.15);padding:10px 10px 0 28px;font-size:6px;line-height:19px;color:var(--text)">
    <li>Lorem ipsum dolor sit amet</li><li>Lorem ipsum dolor sit amet</li><li>Lorem ipsum dolor sit amet</li><li>Lorem ipsum dolor sit amet</li><li>Lorem ipsum dolor sit amet</li><li>Lorem ipsum dolor sit amet</li><li>Lorem ipsum dolor sit amet</li>
  </ol>
  <div class="abs" style="left:230px;top:74px;font-size:15px;font-weight:600;line-height:1.1;color:var(--navy)">Here Goes<br>Title Of Your<br>Agenda</div>
  <div class="abs" style="left:230px;top:130px;font-size:6.5px;color:var(--red)">Here Goes A Short Subtitle</div>
  <div class="page-no">12</div><div class="rail"><span>Ledger Lanternfox</span></div>
</section>

<!-- 13 -->
<section class="slide">
  <div class="title" style="left:14px;top:12px">Title And Body Slide</div><div class="dash" style="left:14px;top:33px"></div>
  <div class="watermark">Ledger Lanternfox</div>
  <div class="page-no">13</div><div class="rail"><span>Ledger Lanternfox</span></div>
</section>
<!-- 14 -->
<section class="slide">
  <div class="dash" style="left:32px;top:38px"></div>
  <div class="watermark">Ledger Lanternfox</div>
  <div class="page-no l" style="left:28px">14</div><div class="rail left"><span>Ledger Lanternfox</span></div>
</section>
<!-- 15 -->
<section class="slide">
  <div class="title" style="left:18px;top:12px">Title And Body Slide</div><div class="dash" style="left:18px;top:33px"></div>
  <div class="page-no">15</div><div class="rail"><span>Ledger Lanternfox</span></div>
</section>
<!-- 16 -->
<section class="slide bg-navy">
  <div class="dash" style="left:30px;top:34px"></div>
  <div class="page-no" style="left:28px;color:#fff">16</div><div class="rail left"><span>Ledger Lanternfox</span></div>
</section>
<!-- 17 -->
<section class="slide bg-navy">
  <div class="title white" style="left:18px;top:12px">Title And Body Slide</div><div class="dash" style="left:18px;top:33px"></div>
  <div class="page-no" style="color:#fff">17</div><div class="rail dark"><span>Ledger Lanternfox</span></div>
</section>
<!-- 18 -->
<section class="slide bg-navy">
  <div class="dash" style="left:34px;top:36px"></div>
  <div class="page-no" style="left:28px;color:#fff">18</div><div class="rail left dark"><span>Ledger Lanternfox</span></div>
</section>
<!-- 19 -->
<section class="slide">
  <div class="dash" style="left:16px;top:36px"></div>
  <div class="page-no">19</div><div class="rail"><span>Ledger Lanternfox</span></div>
</section>
<!-- 20 -->
<section class="slide">
  <div class="dash" style="left:30px;top:36px"></div>
  <div class="page-no" style="left:28px">20</div><div class="rail left"><span>Ledger Lanternfox</span></div>
</section>
<!-- 21 -->
<section class="slide">
  <div class="logo dark big" style="left:150px;top:82px;font-size:16px">Ledger Lanternfox</div>
  <div class="abs bg-red" style="left:0;right:0;bottom:0;height:8px"></div>
</section>

<!-- 22 slide break -->
<section class="slide">
  <div class="photo" role="img" aria-label="Blue-tinted photo of a workspace"></div>
  <div class="abs" style="left:22px;top:40px;font-size:54px;font-weight:600;color:rgba(255,255,255,.18);line-height:1">01</div>
  <div class="abs" style="left:45px;top:66px;font-size:30px;font-weight:300;color:#fff;line-height:.95">Slide<br>Break</div>
  <p class="abs tiny" style="left:45px;top:138px;width:175px">Lorem ipsum dolor sit amet, consectetur adipiscing elit, sed do eiusmod tempor incididunt ut labore et dolore magna aliqua. Lorem ipsum dolor sit amet, consectetur adipiscing elit, sed do eiusmod tempor incididunt ut labore et dolore magna aliqua.</p>
</section>

<!-- 23 demo -->
<section class="slide">
  <div class="photo" role="img" aria-label="Blue-tinted photo of a person typing"></div>
  <div class="demo-ring" style="left:104px;top:20px;width:180px;height:180px;border:1.2px solid #fff;color:var(--red)">
    <h3>DEMO</h3>
    <p class="tiny" style="color:#fff">Lorem ipsum dolor sit amet, consectetur adipiscing elit, sed do eiusmod tempor incididunt ut labore et dolore magna aliqua. Lorem ipsum dolor sit amet, consectetur adipiscing elit, sed do eiusmod tempor incididunt ut labore. Lorem ipsum dolor sit amet.</p>
  </div>
</section>

<!-- 24 demo -->
<section class="slide bg-navy">
  <div class="demo-ring" style="left:100px;top:16px;width:188px;height:188px;background:#1f4c90;border:5px solid #255299;color:#fff">
    <h3>DEMO</h3>
    <p class="tiny">Lorem ipsum dolor sit amet, consectetur adipiscing elit, sed do eiusmod tempor incididunt ut labore et dolore magna aliqua. Lorem ipsum dolor sit amet, consectetur adipiscing elit, sed do eiusmod tempor incididunt ut labore et dolore magna aliqua. Lorem ipsum dolor sit amet.</p>
  </div>
</section>

<!-- 25 demo -->
<section class="slide">
  <div class="photo" role="img" aria-label="Blue-tinted photo of a laptop keyboard"></div>
  <div class="abs" style="left:0;right:0;top:12px;height:1px;background:rgba(255,255,255,.4)"></div>
  <div class="logo" style="left:28px;top:100px;font-size:9px">Ledger Lanternfox</div>
  <div class="abs" style="left:166px;top:70px;width:2px;height:78px;background:var(--red)"></div>
  <div class="abs" style="left:172px;top:70px;background:var(--red);color:#fff;font-size:10px;font-weight:600;padding:0 5px;border-radius:3px">DEMO</div>
  <p class="abs" style="left:172px;top:90px;width:180px;font-size:6.5px;line-height:1.3;color:#fff">Lorem ipsum dolor sit amet, consectetur adipiscing elit, sed do eiusmod tempor incididunt ut labore et dolore magna aliqua. Lorem ipsum dolor sit amet, consectetur adipiscing elit, sed do eiusmod tempor incididunt ut labore et dolore magna aliqua.</p>
</section>

<!-- 26 pic and text -->
<section class="slide">
  <div class="title" style="left:20px;top:58px;font-size:18px">Pic And Text</div><div class="dash" style="left:20px;top:83px"></div>
  <p class="abs body" style="left:20px;top:92px;width:135px;text-align:justify">Lorem ipsum dolor sit amet, consectetur adipiscing elit, sed do eiusmod tempor incididunt ut labore et dolore magna aliqua. Lorem ipsum dolor sit amet, consectetur adipiscing elit, sed do eiusmod tempor incididunt ut labore et dolore magna aliqua. Ut enim ad minim veniam, quis nostrud exercitation ullamco laboris nisi ut aliquip.</p>
  <div class="abs bg-red" style="left:192px;top:24px;width:92px;height:78px"></div>
  <div class="abs photo light" role="img" aria-label="Photo of hands at a keyboard and monitor" style="left:200px;top:40px;width:160px;height:125px;inset:auto;"></div>
  <div class="page-no">26</div><div class="rail"><span>Ledger Lanternfox</span></div>
</section>

<!-- 27 -->
<section class="slide">
  <div class="abs bg-red" style="left:184px;top:48px;width:40px;height:2px"></div>
  <div class="abs bg-navy" style="left:88px;top:142px;width:300px;height:76px;border-top-left-radius:26px"></div>
  <div class="rail" style="bottom:76px"><span>Ledger Lanternfox</span></div>
</section>

<!-- 28 icons -->
<section class="slide">
  <div class="abs bg-navy" style="left:0;top:0;width:366px;height:108px"></div>
  <div class="title white center" style="top:30px;right:22px;font-size:16px">Here Add Awesome Text</div>
  <div class="dash" style="left:176px;top:55px"></div>
  <svg class="abs" style="left:50px;top:90px" width="250" height="36" viewBox="0 0 250 36">
    <g fill="#e8282b" stroke="#fff" stroke-width="1.5">
      <circle cx="18" cy="18" r="15"/><circle cx="125" cy="18" r="15"/><circle cx="232" cy="18" r="15"/>
    </g>
    <g fill="none" stroke="#fff" stroke-width="1.2">
      <circle cx="18" cy="18" r="6"/><circle cx="18" cy="18" r="2.5"/>
      <path d="M119 24l10-12M123 12h6v6"/>
      <path d="M226 22h12M226 18h12M226 14h8"/>
    </g>
  </svg>
  <div class="abs" style="left:20px;top:132px;width:320px;display:grid;grid-template-columns:repeat(3,1fr);gap:14px;text-align:center">
    <div><h5 style="font-size:5.5px;font-weight:600">Project name</h5><p class="body" style="font-size:4.3px">Lorem ipsum dolor sit amet, nec an dictas equidem appellantur, ut has commune accommodare. Mea illum, ludus solet idque.</p></div>
    <div><h5 style="font-size:5.5px;font-weight:600">Project name</h5><p class="body" style="font-size:4.3px">Lorem ipsum dolor sit amet, nec an dictas equidem appellantur, ut has commune accommodare. Mea illum, ludus solet idque.</p></div>
    <div><h5 style="font-size:5.5px;font-weight:600">Project name</h5><p class="body" style="font-size:4.3px">Lorem ipsum dolor sit amet, nec an dictas equidem appellantur, ut has commune accommodare. Mea illum, ludus solet idque.</p></div>
  </div>
  <div class="page-no l" style="left:6px">28</div><div class="rail"><span>Ledger Lanternfox</span></div>
</section>

<!-- 29 three columns -->
<section class="slide">
  <div class="title center" style="top:18px;right:22px">3 Columns Slide</div><div class="dash" style="left:176px;top:39px"></div>
  <div class="card c-red" style="left:44px;top:90px;width:88px;height:76px;color:#fff"><span class="ic" style="color:var(--red)"></span><h4>Project name here</h4><p>Lorem ipsum dolor sit amet, nec an dictas equidem appellantur, ut has commune accommodare. Mea illum, ludus solet idque.</p></div>
  <div class="card c-navy" style="left:142px;top:90px;width:88px;height:76px"><span class="ic" style="color:var(--navy)"></span><h4>Project name here</h4><p>Lorem ipsum dolor sit amet, nec an dictas equidem appellantur, ut has commune accommodare. Mea illum, ludus solet idque.</p></div>
  <div class="card c-gray" style="left:240px;top:90px;width:88px;height:76px"><span class="ic" style="color:var(--gray)"></span><h4>Project name here</h4><p>Lorem ipsum dolor sit amet, nec an dictas equidem appellantur, ut has commune accommodare. Mea illum, ludus solet idque.</p></div>
  <div class="page-no">29</div><div class="rail"><span>Ledger Lanternfox</span></div>
</section>

<!-- 30 four columns -->
<section class="slide">
  <div class="title center" style="top:18px;right:22px">4 Column Slide</div><div class="dash" style="left:176px;top:39px"></div>
  <div class="card c-red" style="left:20px;top:84px;width:82px;height:100px"><span class="ic" style="color:var(--red)"></span><h4>Project name here</h4><p>Lorem ipsum dolor sit amet, nec an dictas equidem appellantur, ut has commune accommodare. Mea illum, ludus solet idque. Lorem ipsum dolor sit amet, nec an dictas.</p></div>
  <div class="card c-navy" style="left:107px;top:84px;width:82px;height:100px"><span class="ic" style="color:var(--navy)"></span><h4>Project name here</h4><p>Lorem ipsum dolor sit amet, nec an dictas equidem appellantur, ut has commune accommodare. Mea illum, ludus solet idque. Lorem ipsum dolor sit amet, nec an dictas.</p></div>
  <div class="card c-deep" style="left:194px;top:84px;width:82px;height:100px"><span class="ic" style="color:var(--ink)"></span><h4>Project name here</h4><p>Lorem ipsum dolor sit amet, nec an dictas equidem appellantur, ut has commune accommodare. Mea illum, ludus solet idque. Lorem ipsum dolor sit amet, nec an dictas.</p></div>
  <div class="card c-gray" style="left:281px;top:84px;width:82px;height:100px"><span class="ic" style="color:var(--gray)"></span><h4>Project name here</h4><p>Lorem ipsum dolor sit amet, nec an dictas equidem appellantur, ut has commune accommodare. Mea illum, ludus solet idque. Lorem ipsum dolor sit amet, nec an dictas.</p></div>
  <div class="page-no">30</div><div class="rail"><span>Ledger Lanternfox</span></div>
</section>

<!-- 31 five columns -->
<section class="slide">
  <div class="title center" style="top:18px;right:22px">5 Column Slide</div><div class="dash" style="left:176px;top:39px"></div>
  <div class="card c-navy" style="left:42px;top:68px;width:92px;height:56px;padding-top:6px"><h4>Project name here</h4><p>Lorem ipsum dolor sit amet, nec an dictas equidem appellantur, ut has commune accommodare. Mea illum, ludus solet idque.</p></div>
  <div class="card c-navy" style="left:140px;top:68px;width:92px;height:56px;padding-top:6px"><h4>Project name here</h4><p>Lorem ipsum dolor sit amet, nec an dictas equidem appellantur, ut has commune accommodare. Mea illum, ludus solet idque.</p></div>
  <div class="card c-navy" style="left:238px;top:68px;width:92px;height:56px;padding-top:6px"><h4>Project name here</h4><p>Lorem ipsum dolor sit amet, nec an dictas equidem appellantur, ut has commune accommodare. Mea illum, ludus solet idque.</p></div>
  <div class="card c-navy" style="left:90px;top:132px;width:92px;height:56px;padding-top:6px"><h4>Project name here</h4><p>Lorem ipsum dolor sit amet, nec an dictas equidem appellantur, ut has commune accommodare. Mea illum, ludus solet idque.</p></div>
  <div class="card c-navy" style="left:188px;top:132px;width:92px;height:56px;padding-top:6px"><h4>Project name here</h4><p>Lorem ipsum dolor sit amet, nec an dictas equidem appellantur, ut has commune accommodare. Mea illum, ludus solet idque.</p></div>
  <div class="page-no">31</div><div class="rail"><span>Ledger Lanternfox</span></div>
</section>

<!-- 32 screenshot -->
<section class="slide">
  <div class="abs bg-navy" style="left:0;top:0;width:270px;height:218px;clip-path:polygon(0 0,62% 0,100% 100%,0 100%)"></div>
  <div class="title white" style="left:20px;top:72px;font-size:14px;line-height:1.15">A Place for<br>Screenshot</div>
  <div class="dash" style="left:20px;top:110px"></div>
  <p class="abs tiny" style="left:20px;top:118px;width:120px">Lorem ipsum dolor sit amet, consectetur adipiscing elit, sed do eiusmod tempor ela beta on lopun ekerim dolor on lor ti.</p>
  <div class="abs" style="left:152px;top:50px;width:210px;height:134px;background:#222;border-radius:5px;padding:5px"><div style="width:100%;height:100%;background:#8f8f8f;display:flex;align-items:center;justify-content:center;color:#fff;font-size:6.5px;font-weight:600">HERE YOU CAN ADD A SCREENSHOT</div></div>
  <div class="abs" style="left:132px;top:184px;width:250px;height:6px;background:#cfcfcf;border-radius:0 0 6px 6px"></div>
  <div class="page-no">32</div><div class="rail"><span>Ledger Lanternfox</span></div>
</section>

<!-- 33 six columns -->
<section class="slide">
  <div class="title center" style="top:18px;right:22px">6 Columns Slide</div><div class="dash" style="left:176px;top:39px"></div>
  <svg class="abs" style="left:34px;top:74px" width="210" height="120" viewBox="0 0 210 120">
    <g fill="none" stroke="#1b4585" stroke-width="1">
      <rect x="0" y="0" width="10" height="10"/><path d="M2 4h6M2 7h6"/>
      <path d="M0 50l5-8 5 8M2 50v-4h6v4"/>
      <circle cx="5" cy="84" r="5"/><path d="M5 81v3h3"/>
      <rect x="166" y="0" width="10" height="10"/><path d="M168 4h6M168 7h6"/>
      <path d="M166 50l5-8 5 8M168 50v-4h6v4"/>
      <circle cx="171" cy="84" r="5"/><path d="M171 81v3h3"/>
    </g>
  </svg>
  <div class="abs" style="left:60px;top:70px;width:290px;display:grid;grid-template-columns:1fr 1fr;column-gap:40px;row-gap:12px">
    <div><h5 style="font-size:5.5px;font-weight:600">Project name</h5><p class="body" style="font-size:4.3px">Lorem ipsum dolor sit amet, nec an dictas equidem appellantur, ut has commune accommodare. Mea illum, ludus solet idque.</p></div>
    <div><h5 style="font-size:5.5px;font-weight:600">Project name</h5><p class="body" style="font-size:4.3px">Lorem ipsum dolor sit amet, nec an dictas equidem appellantur, ut has commune accommodare. Mea illum, ludus solet idque.</p></div>
    <div><h5 style="font-size:5.5px;font-weight:600">Project name</h5><p class="body" style="font-size:4.3px">Lorem ipsum dolor sit amet, nec an dictas equidem appellantur, ut has commune accommodare. Mea illum, ludus solet idque.</p></div>
    <div><h5 style="font-size:5.5px;font-weight:600">Project name</h5><p class="body" style="font-size:4.3px">Lorem ipsum dolor sit amet, nec an dictas equidem appellantur, ut has commune accommodare. Mea illum, ludus solet idque.</p></div>
    <div><h5 style="font-size:5.5px;font-weight:600">Project name</h5><p class="body" style="font-size:4.3px">Lorem ipsum dolor sit amet, nec an dictas equidem appellantur, ut has commune accommodare. Mea illum, ludus solet idque.</p></div>
    <div><h5 style="font-size:5.5px;font-weight:600">Project name</h5><p class="body" style="font-size:4.3px">Lorem ipsum dolor sit amet, nec an dictas equidem appellantur, ut has commune accommodare. Mea illum, ludus solet idque.</p></div>
  </div>
  <div class="page-no">33</div><div class="rail"><span>Ledger Lanternfox</span></div>
</section>

<!-- 34 table with checks -->
<section class="slide">
  <div class="title center" style="top:12px;right:22px">Table Slide</div><div class="dash" style="left:176px;top:33px"></div>
  <table class="tbl redhead" style="left:20px;top:50px;width:340px">
    <tr><th style="background:#fff"></th><th>Your Text Here</th><th>Your Text Here</th><th>Your Text Here</th><th>Your Text Here</th></tr>
    <tr><td class="row-h">You can replace this text</td><td>2200</td><td style="color:var(--navy)">&#10004;</td><td>50%</td><td>2200</td></tr>
    <tr><td class="row-h">You can replace this text</td><td>3600</td><td style="color:var(--navy)">&#10006;</td><td>50%</td><td>3600</td></tr>
    <tr><td class="row-h">You can replace this text</td><td>2200</td><td style="color:var(--navy)">&#10004;</td><td>50%</td><td>2200</td></tr>
    <tr><td class="row-h">You can replace this text</td><td>3600</td><td style="color:var(--navy)">&#10006;</td><td>50%</td><td>3600</td></tr>
    <tr><td class="row-h">You can replace this text</td><td>2200</td><td style="color:var(--navy)">&#10004;</td><td>50%</td><td>2200</td></tr>
    <tr><td class="row-h">You can replace this text</td><td>3600</td><td style="color:var(--navy)">&#10006;</td><td>50%</td><td>3600</td></tr>
    <tr><td class="row-h">You can replace this text</td><td>2200</td><td style="color:var(--navy)">&#10004;</td><td>50%</td><td>2200</td></tr>
  </table>
  <div class="page-no">34</div><div class="rail"><span>Ledger Lanternfox</span></div>
</section>

<!-- 35 table navy -->
<section class="slide">
  <div class="abs bg-navy" style="left:0;top:0;width:208px;height:218px"></div>
  <div class="title white" style="left:18px;top:100px;font-size:14px">Table Slide</div><div class="dash" style="left:18px;top:121px"></div>
  <div class="abs" style="left:138px;top:34px;width:212px;height:158px;background:#fff;box-shadow:0 2px 8px rgba(0,0,0,.2);border-radius:4px"></div>
  <table class="tbl" style="left:148px;top:44px;width:192px">
    <tr><th>Text</th><th>Text</th><th>Text</th><th>Text</th><th>Text</th></tr>
    <tr><td>Data</td><td>Data</td><td>Data</td><td>Data</td><td>Data</td></tr>
    <tr><td>Data</td><td>Data</td><td>Data</td><td>Data</td><td>Data</td></tr>
    <tr><td>Data</td><td>Data</td><td>Data</td><td>Data</td><td>Data</td></tr>
    <tr><td>Data</td><td>Data</td><td>Data</td><td>Data</td><td>Data</td></tr>
    <tr><td>Data</td><td>Data</td><td>Data</td><td>Data</td><td>Data</td></tr>
    <tr><td>Data</td><td>Data</td><td>Data</td><td>Data</td><td>Data</td></tr>
  </table>
  <div class="page-no">35</div><div class="rail"><span>Ledger Lanternfox</span></div>
</section>

<!-- 36 table -->
<section class="slide">
  <div class="title center" style="top:14px;right:22px">Table Slide</div><div class="dash" style="left:176px;top:35px"></div>
  <table class="tbl" style="left:30px;top:56px;width:318px">
    <tr><th>Text</th><th>Text</th><th>Text</th><th>Text</th><th>Text</th></tr>
    <tr><td>Data</td><td>Data</td><td>Data</td><td>Data</td><td>Data</td></tr>
    <tr><td>Data</td><td>Data</td><td>Data</td><td>Data</td><td>Data</td></tr>
    <tr><td>Data</td><td>Data</td><td>Data</td><td>Data</td><td>Data</td></tr>
    <tr><td>Data</td><td>Data</td><td>Data</td><td>Data</td><td>Data</td></tr>
    <tr><td>Data</td><td>Data</td><td>Data</td><td>Data</td><td>Data</td></tr>
    <tr><td>Data</td><td>Data</td><td>Data</td><td>Data</td><td>Data</td></tr>
  </table>
  <div class="page-no">36</div><div class="rail"><span>Ledger Lanternfox</span></div>
</section>

<!-- 37 smart art -->
<section class="slide">
  <div class="title" style="left:20px;top:12px">Smart Art Slide</div><div class="dash" style="left:20px;top:33px"></div>
  <svg class="abs" style="left:20px;top:64px" width="14" height="110" viewBox="0 0 14 110">
    <g fill="none" stroke="#1b4585" stroke-width="1"><rect x="1" y="1" width="10" height="10"/><path d="M1 50l10-6M3 52l8-4"/><circle cx="6" cy="96" r="5"/></g>
  </svg>
  <div class="abs" style="left:38px;top:60px;width:120px;display:grid;row-gap:10px">
    <div><h5 style="font-size:5px;font-weight:600;color:var(--navy)">Lorem ipsum dolor</h5><p class="body" style="font-size:4.2px">Lorem ipsum dolor sit amet, consectetur adipiscing elit, sed do eiusmod tempor ela beta on lopun ekerim dolor on lor ti.</p></div>
    <div><h5 style="font-size:5px;font-weight:600;color:var(--navy)">Lorem ipsum dolor</h5><p class="body" style="font-size:4.2px">Lorem ipsum dolor sit amet, consectetur adipiscing elit, sed do eiusmod tempor ela beta on lopun ekerim dolor on lor ti.</p></div>
    <div><h5 style="font-size:5px;font-weight:600;color:var(--navy)">Lorem ipsum dolor</h5><p class="body" style="font-size:4.2px">Lorem ipsum dolor sit amet, consectetur adipiscing elit, sed do eiusmod tempor ela beta on lopun ekerim dolor on lor ti.</p></div>
  </div>
  <svg class="abs" style="left:190px;top:48px" width="160" height="148" viewBox="0 0 160 148">
    <path d="M80 4L118 72H42Z" fill="#1b4585"/>
    <path d="M42 76H118L80 142Z" fill="#1b4585"/>
    <path d="M38 76L76 144H0Z" fill="#e8282b"/>
    <path d="M122 76L160 144H84Z" fill="#7d7d7d"/>
    <g fill="#fff" font-family="Poppins,sans-serif" text-anchor="middle">
      <text x="80" y="40" font-size="6" font-weight="600">Project</text><text x="80" y="48" font-size="6" font-weight="600">name</text>
      <text x="38" y="108" font-size="5.5" font-weight="600">Project name</text>
      <text x="122" y="108" font-size="5.5" font-weight="600">Project name</text>
      <text x="80" y="92" font-size="3.5">Lorem ipsum dolor</text>
      <text x="38" y="118" font-size="3.5">Lorem ipsum dolor</text>
      <text x="122" y="118" font-size="3.5">Lorem ipsum dolor</text>
    </g>
  </svg>
  <div class="page-no">37</div><div class="rail"><span>Ledger Lanternfox</span></div>
</section>

<!-- 38 quotes -->
<section class="slide">
  <div class="title center" style="top:18px;right:22px">Here is Quotes</div><div class="dash" style="left:176px;top:39px"></div>
  <div class="abs" style="left:28px;top:52px;font-size:26px;font-weight:700;color:var(--red)">&rdquo;</div>
  <div class="abs" style="left:205px;top:52px;font-size:26px;font-weight:700;color:var(--navy)">&rdquo;</div>
  <p class="abs body" style="left:28px;top:90px;width:150px">Lorem ipsum dolor sit amet, consectetur adipiscing elit, sed do eiusmod tempor incididunt ut labore et dolore magna aliqua. Lorem ipsum dolor sit amet, consectetur adipiscing elit.</p>
  <p class="abs body" style="left:205px;top:90px;width:150px">Lorem ipsum dolor sit amet, consectetur adipiscing elit, sed do eiusmod tempor incididunt ut labore et dolore magna aliqua. Lorem ipsum dolor sit amet, consectetur adipiscing elit.</p>
  <div class="abs" style="left:30px;top:160px;width:16px;height:16px;border-radius:50%;background:#e6e6e6"></div>
  <div class="abs" style="left:52px;top:161px;font-size:5px;color:var(--navy)">Your Name<br><span style="color:#888;font-size:4px">Founder</span></div>
  <div class="abs" style="left:207px;top:160px;width:16px;height:16px;border-radius:50%;background:#e6e6e6"></div>
  <div class="abs" style="left:229px;top:161px;font-size:5px;color:var(--navy)">Your Name<br><span style="color:#888;font-size:4px">Founder</span></div>
  <div class="page-no">38</div><div class="rail"><span>Ledger Lanternfox</span></div>
</section>

<!-- 39 statistics circles -->
<section class="slide">
  <div class="title center" style="top:18px;right:22px">Here Is Statistics</div><div class="dash" style="left:176px;top:39px"></div>
  <svg class="abs" style="left:20px;top:64px" width="170" height="140" viewBox="0 0 170 140">
    <circle cx="64" cy="70" r="62" fill="#1b4585"/>
    <circle cx="64" cy="96" r="36" fill="#e8282b"/>
    <circle cx="64" cy="118" r="16" fill="#3d3d3d"/>
    <g fill="#fff" font-size="13" font-weight="600" text-anchor="middle" font-family="Poppins,sans-serif"><text x="64" y="32">$</text><text x="64" y="80">$</text><text x="64" y="123" font-size="9">$</text></g>
    <g fill="#1b4585" font-size="9" font-weight="600" font-family="Poppins,sans-serif"><text x="138" y="30">5M</text><text x="138" y="64">2M</text><text x="138" y="106">1M</text></g>
  </svg>
  <div class="abs" style="left:216px;top:88px;display:grid;row-gap:11px;width:130px">
    <div style="display:flex;gap:6px"><span style="width:11px;height:11px;background:var(--navy);color:#fff;font-size:7px;text-align:center;line-height:11px;flex:none">&#10003;</span><div><h5 style="font-size:5px;font-weight:600">Lorem ipsum dolor</h5><p class="body" style="font-size:4.2px">Lorem ipsum dolor sit amet, consectetur adipiscing elit, sed do eiusmod tempor</p></div></div>
    <div style="display:flex;gap:6px"><span style="width:11px;height:11px;background:var(--red);color:#fff;font-size:7px;text-align:center;line-height:11px;flex:none">&#10003;</span><div><h5 style="font-size:5px;font-weight:600">Lorem ipsum dolor</h5><p class="body" style="font-size:4.2px">Lorem ipsum dolor sit amet, consectetur adipiscing elit, sed do eiusmod tempor</p></div></div>
    <div style="display:flex;gap:6px"><span style="width:11px;height:11px;background:var(--charcoal);color:#fff;font-size:7px;text-align:center;line-height:11px;flex:none">&#10003;</span><div><h5 style="font-size:5px;font-weight:600">Lorem ipsum dolor</h5><p class="body" style="font-size:4.2px">Lorem ipsum dolor sit amet, consectetur adipiscing elit, sed do eiusmod tempor</p></div></div>
  </div>
  <div class="page-no">39</div><div class="rail"><span>Ledger Lanternfox</span></div>
</section>

<!-- 40 percentages -->
<section class="slide">
  <div class="title center" style="top:18px;right:22px">Here Add Your Title</div><div class="dash" style="left:176px;top:39px"></div>
  <p class="abs body" style="left:60px;top:46px;width:250px;text-align:center">Lorem Ipsum is simply dummy text of the printing and typesetting industry. Lorem Ipsum has been the industry's standard dummy text ever since the 1500s, when an unknown printer took a galley of type and scrambled it to make a type specimen book.</p>
  <svg class="abs" style="left:44px;top:94px" width="280" height="60" viewBox="0 0 280 60">
    <g fill="none" stroke-width="4">
      <circle cx="40" cy="30" r="24" stroke="#e6e6e6"/><circle cx="40" cy="30" r="24" stroke="#e8282b" stroke-dasharray="75.4 150.8" transform="rotate(-90 40 30)"/>
      <circle cx="140" cy="30" r="24" stroke="#e6e6e6"/><circle cx="140" cy="30" r="24" stroke="#e8282b" stroke-dasharray="113.1 150.8" transform="rotate(-90 140 30)"/>
      <circle cx="240" cy="30" r="24" stroke="#e6e6e6"/><circle cx="240" cy="30" r="24" stroke="#e8282b" stroke-dasharray="60.3 150.8" transform="rotate(-90 240 30)"/>
    </g>
    <g fill="#1b4585" font-size="10" font-weight="600" text-anchor="middle" font-family="Poppins,sans-serif"><text x="40" y="34">50%</text><text x="140" y="34">75%</text><text x="240" y="34">40%</text></g>
  </svg>
  <div class="abs body" style="left:54px;top:162px;width:60px;text-align:center">Lorem ipsum dolor amet sed consectetur dolor</div>
  <div class="abs body" style="left:154px;top:162px;width:60px;text-align:center">Lorem ipsum dolor amet sed consectetur dolor</div>
  <div class="abs body" style="left:254px;top:162px;width:60px;text-align:center">Lorem ipsum dolor amet sed consectetur dolor</div>
</section>

<!-- 41 statistics chart -->
<section class="slide">
  <div class="title center" style="top:14px;right:22px">Here is Statistics</div><div class="dash" style="left:176px;top:35px"></div>
  <div class="abs bg-navy" style="left:14px;top:72px;width:92px;height:56px;color:#fff;text-align:center;padding-top:14px"><div style="font-size:13px">$0.5M</div><div style="font-size:5px">Revenue</div></div>
  <div class="abs" style="left:14px;top:128px;width:92px;height:56px;border:1px solid var(--red);color:var(--red);text-align:center;padding-top:14px"><div style="font-size:13px">-0.28%</div><div style="font-size:5px">Revenue</div></div>
  <svg class="abs" style="left:112px;top:66px" width="250" height="128" viewBox="0 0 250 128">
    <g fill="#888" font-size="4" font-family="Poppins,sans-serif"><text x="0" y="10">$50,000</text><text x="0" y="28">$40,000</text><text x="0" y="46">$30,000</text><text x="0" y="64">$20,000</text><text x="0" y="82">$10,000</text><text x="10" y="100">$0</text></g>
    <g stroke="#eee" stroke-width=".6"><path d="M24 8H245M24 26H245M24 44H245M24 62H245M24 80H245M24 98H245"/></g>
    <polyline fill="none" stroke="#e8282b" stroke-width="1" points="30,90 40,84 50,88 60,70 70,78 80,66 90,74 100,60 110,70 120,58 130,66 140,54 150,64 160,50 170,60 180,42 190,56 200,38 210,48 220,30 230,40 240,12"/>
    <g fill="#888" font-size="3.5" font-family="Poppins,sans-serif"><text x="28" y="108">Jan</text><text x="46" y="108">Feb</text><text x="64" y="108">Mar</text><text x="82" y="108">Apr</text><text x="100" y="108">May</text><text x="118" y="108">Jun</text><text x="136" y="108">Jul</text><text x="154" y="108">Aug</text><text x="172" y="108">Sep</text><text x="190" y="108">Oct</text><text x="208" y="108">Nov</text><text x="226" y="108">Dec</text></g>
  </svg>
  <div class="page-no">41</div><div class="rail"><span>Ledger Lanternfox</span></div>
</section>

<!-- 42 timeline -->
<section class="slide">
  <div class="title center" style="top:18px;right:22px">Company Timeline</div><div class="dash" style="left:176px;top:39px"></div>
  <div class="chev c-red" style="left:24px">STEP 01</div>
  <div class="chev c-navy" style="left:84px">STEP 02</div>
  <div class="chev c-red" style="left:144px">STEP 03</div>
  <div class="chev c-navy" style="left:204px">STEP 04</div>
  <div class="chev c-red" style="left:264px">STEP 05</div>
  <div class="step-text" style="left:24px"><h5>Project name</h5><p>Lorem Ipsum is simply dummy text, unknown printer took a galley of type and scrambled it.</p></div>
  <div class="step-text" style="left:86px"><h5>Project name</h5><p>Lorem Ipsum is simply dummy text, unknown printer took a galley of type and scrambled it.</p></div>
  <div class="step-text" style="left:148px"><h5>Project name</h5><p>Lorem Ipsum is simply dummy text, unknown printer took a galley of type and scrambled it.</p></div>
  <div class="step-text" style="left:210px"><h5>Project name</h5><p>Lorem Ipsum is simply dummy text, unknown printer took a galley of type and scrambled it.</p></div>
  <div class="step-text" style="left:272px"><h5>Project name</h5><p>Lorem Ipsum is simply dummy text, unknown printer took a galley of type and scrambled it.</p></div>
  <div class="page-no">42</div><div class="rail"><span>Ledger Lanternfox</span></div>
</section>

<!-- 43 Q&A -->
<section class="slide">
  <div class="title center" style="top:14px;right:22px">Q&amp;A Slide</div><div class="dash" style="left:176px;top:35px"></div>
  <div class="qa-row" style="left:44px;top:56px"><b class="c-navy">Q</b><p>Lorem Ipsum is simply dummy unknown printer took a galley of type and scrambled it to make.</p></div>
  <div class="qa-row" style="left:44px;top:88px"><b class="c-navy">Q</b><p>Lorem Ipsum is simply dummy unknown printer took a galley of type and scrambled it to make.</p></div>
  <div class="qa-row" style="left:44px;top:120px"><b class="c-navy">Q</b><p>Lorem Ipsum is simply dummy unknown printer took a galley of type and scrambled it to make.</p></div>
  <div class="qa-row" style="left:44px;top:152px"><b class="c-navy">Q</b><p>Lorem Ipsum is simply dummy unknown printer took a galley of type and scrambled it to make.</p></div>
  <div class="qa-row" style="left:208px;top:56px"><b class="c-red">A</b><p>type and scrambled it to make. Lorem Ipsum is simply dummy unknown printer took a galley of</p></div>
  <div class="qa-row" style="left:208px;top:88px"><b class="c-red">A</b><p>Lorem Ipsum is simply dummy unknown printer took a galley of type and scrambled it to make.</p></div>
  <div class="qa-row" style="left:208px;top:120px"><b class="c-red">A</b><p>Lorem Ipsum is simply dummy unknown printer took a galley of type and scrambled it to make.</p></div>
  <div class="qa-row" style="left:208px;top:152px"><b class="c-red">A</b><p>Lorem Ipsum is simply dummy unknown printer took a galley of type and scrambled it to make.</p></div>
  <div class="page-no">43</div><div class="rail"><span>Ledger Lanternfox</span></div>
</section>

<!-- 44 thank you -->
<section class="slide">
  <div class="logo dark" style="left:44px;top:46px">Ledger Lanternfox</div>
  <div class="abs bg-navy" style="left:44px;top:70px;width:146px;height:120px"></div>
  <svg class="abs" style="left:54px;top:80px" width="130" height="100" viewBox="0 0 130 100">
    <g fill="#fff" font-family="Poppins,sans-serif" font-size="4.5">
      <circle cx="5" cy="6" r="4" fill="none" stroke="#fff" stroke-width=".8"/><path d="M1 6h8M5 2v8" stroke="#fff" stroke-width=".6"/><text x="16" y="8">www.ledgerlanternfox.example</text>
      <path d="M1 38h8l-4 5z" fill="#fff"/><text x="16" y="38">Here to write your</text><text x="16" y="44">Company address</text>
      <rect x="1" y="78" width="8" height="6" fill="none" stroke="#fff" stroke-width=".8"/><path d="M1 78l4 3 4-3" fill="none" stroke="#fff" stroke-width=".8"/><text x="16" y="83">hello@ledgerlanternfox.example</text>
    </g>
    <g stroke="rgba(255,255,255,.3)" stroke-width=".6"><path d="M0 22H130M0 60H130"/></g>
  </svg>
  <div class="abs" style="left:205px;top:98px;font-size:20px;font-weight:600;color:var(--navy)">THANK YOU</div>
</section>

<!-- 45 questions -->
<section class="slide">
  <svg class="abs" style="left:80px;top:20px" width="230" height="180" viewBox="0 0 230 180">
    <path d="M8 30L220 8L212 138L70 146L50 172L48 148L14 150Z" fill="#fff" stroke="#1b4585" stroke-width="1.5"/>
    <path d="M18 22L212 2" stroke="#e8282b" stroke-width="1.5"/>
    <path d="M2 44L8 156L40 154" fill="none" stroke="#e8282b" stroke-width="1.5"/>
  </svg>
  <div class="abs" style="left:0;right:0;top:88px;text-align:center;font-size:22px;font-weight:600;color:var(--navy)">Questions?</div>
</section>

</main>
</body>
</html>
```